Professional & attention grabbing.

A business card design, front and back. I already have a logo I will attach, but I am open to something new as well.
Things to include:
Name:
Title:
Phone:
Email:
Wanting something that is professional but attention grabbing.
Also we do a lot of work using drones on natural gas pipelines (leading the future)if you want to include any of that. I'm open to ideas.
Target Market(s)
Natural gas transmission industry / greenhouse gas mitigation industry
Industry/Entity Type
Business
Colors
Designer to choose colors to be used in the design.
Look and feel
Each slider illustrates characteristics of the customer's brand and the style your logo design should communicate.

```html
<!DOCTYPE html>
<html lang="en">
<head>
<meta charset="utf-8">
<title>Corvale Inspections – Business Card</title>
<link rel="stylesheet" href="https://fonts.googleapis.com/css2?family=Open+Sans:ital,wght@0,400;0,600;0,800;1,400&display=swap">
<style>
  :root {
    --page-bg: #e9e7e4;
    --card-white: #ffffff;
    --brand-red: #c41f26;
    --brand-red-soft: #cf3a40;
    --charcoal: #3a3a3c;
    --ink-light: #ffffff;
    --card-shadow: 0 3px 8px rgba(0,0,0,0.35);
  }
  * { box-sizing: border-box; margin: 0; padding: 0; }
  html, body {
    width: 1200px; height: 987px; overflow: hidden;
    background: var(--page-bg);
    font-family: "Open Sans", Arial, sans-serif;
  }
  .canvas { position: relative; width: 1200px; height: 987px; }

  .card {
    position: absolute; left: 293px; width: 615px; height: 352px;
    box-shadow: var(--card-shadow); overflow: hidden;
  }
  .card--front { top: 130px; background: var(--card-white); }
  .card--back  { top: 506px; background: var(--brand-red); }

  /* front */
  .brand-mark {
    position: absolute; top: 72px; left: 0; right: 0;
    display: flex; justify-content: center; align-items: center; gap: 14px;
  }
  .brand-mark__square { width: 34px; height: 34px; background: var(--brand-red); }
  .brand-mark__name {
    font-weight: 800; font-size: 38px; color: var(--charcoal); letter-spacing: -0.5px;
  }

  .info-band {
    position: absolute; top: 211px; left: 0; width: 100%; height: 109px;
    display: flex;
  }
  .info-band__person { width: 330px; background: var(--brand-red); padding: 30px 0 0 39px; color: var(--ink-light); }
  .info-band__contact {
    flex: 1; background: var(--charcoal); padding: 20px 38px 0 0;
    display: flex; flex-direction: column; align-items: flex-end; gap: 5px;
  }
  .person__name { font-weight: 600; font-size: 21px; line-height: 1.15; }
  .person__title { font-size: 16px; }

  .contact-line {
    display: flex; align-items: center; gap: 7px;
    color: var(--ink-light); font-size: 16px; line-height: 19px;
  }
  .contact-line svg { width: 15px; height: 15px; fill: var(--ink-light); }

  /* back */
  .back-texture {
    position: absolute; inset: 0;
    background: linear-gradient(135deg, var(--brand-red-soft), var(--brand-red) 60%);
  }
  .back-lockup {
    position: absolute; top: 118px; left: 0; right: 0; text-align: center; color: var(--ink-light);
  }
  .back-lockup__name { font-weight: 800; font-size: 46px; letter-spacing: -0.5px; }
  .back-lockup__web { font-style: italic; font-size: 15px; letter-spacing: 3px; margin-top: 6px; }
</style>
</head>
<body>
<main class="canvas">

  <section class="card card--front" aria-label="Business card front">
    <div class="brand-mark">
      <span class="brand-mark__square"></span>
      <span class="brand-mark__name">Corvale Inspections</span>
    </div>

    <div class="info-band">
      <div class="info-band__person">
        <p class="person__name">DANA WHITLOCK</p>
        <p class="person__title">CEO/Founder</p>
      </div>
      <div class="info-band__contact">
        <p class="contact-line">555 014 2538
          <svg viewBox="0 0 24 24" aria-hidden="true"><path d="M6.6 10.8a15.1 15.1 0 0 0 6.6 6.6l2.2-2.2a1 1 0 0 1 1-.25 11.4 11.4 0 0 0 3.6.57 1 1 0 0 1 1 1V20a1 1 0 0 1-1 1A17 17 0 0 1 3 4a1 1 0 0 1 1-1h3.5a1 1 0 0 1 1 1c0 1.25.2 2.45.57 3.57a1 1 0 0 1-.25 1z"/></svg>
        </p>
        <p class="contact-line">dana@corvale-mail.com
          <svg viewBox="0 0 24 24" aria-hidden="true"><path d="M2 5h20v14H2z M3.5 6.5 12 13l8.5-6.5" fill="none" stroke="#fff" stroke-width="0"/><path d="M2 5h20v14H2zm2 2v.4l8 5.6 8-5.6V7z" fill-rule="evenodd"/></svg>
        </p>
        <p class="contact-line">www.corvale-site.com
          <svg viewBox="0 0 24 24" aria-hidden="true"><circle cx="12" cy="12" r="10"/><path d="M12 2v20M2 12h20" stroke="#3a3a3c" stroke-width="1.6"/></svg>
        </p>
      </div>
    </div>
  </section>

  <section class="card card--back" aria-label="Business card back">
    <div class="back-texture" role="img" aria-label="Tiled red decorative pattern background"></div>
    <div class="back-lockup">
      <p class="back-lockup__name">Corvale Inspections</p>
      <p class="back-lockup__web">www.corvale-site.com</p>
    </div>
  </section>

</main>
</body>
</html>
```